Website design for Silver Harbor Trading Inc

We are looking to build a website for our company. We are a scrap metal recycling company based out of Los Angeles. We purchase scrap metal in the US and ship them to China for recycling into fresh metal ores to supply industrial users. We would designs that emphasize the color green given our name and the nature of our business. Recycling themes are welcomed. We already have a URL at:
http://silverharbortradinginc.example/
At this point, I would like 4 pages:
- Home page
- About Us
- Resources
- Contact us
Our sister company is Maple Crest Intl Inc and they have a website that we can use as a starting point.
http://www.maplecrest-intl.example/
Our competitor has a website below. However we dislike the design given we believe it looks rather dull.
http://www.orientalloysalvage.example/en/
Lastly, this is for a website shell only. Please design the template, graphics, and color schemes. We will write the contents later.

```html
<!DOCTYPE html>
<html lang="en">
<head>
<meta charset="utf-8">
<title>Contact Us – Silver Harbor Trading</title>
<link href="https://fonts.googleapis.com/css2?family=Roboto:wght@300;400;500;700&display=swap" rel="stylesheet">
<style>
:root{
  --green:#6aaa14;
  --green-dark:#4f8a0a;
  --bar:#3a3a3a;
  --header:#1b1b1b;
  --ink:#222;
  --muted:#9a9a9a;
  --field-border:#e1e1e1;
  --field-bg:#fbfbfb;
  --white:#fff;
}
*{box-sizing:border-box;margin:0;padding:0}
html,body{width:1073px;height:1200px;overflow:hidden}
body{font-family:'Roboto',sans-serif;position:relative;background:var(--header);color:var(--ink)}
.news-bar{position:absolute;top:0;left:0;width:1073px;height:30px;background:var(--bar);color:#eee;font-size:11px;font-weight:300;display:flex;align-items:center;padding-left:218px;white-space:nowrap}
.news-bar .label{color:var(--green);font-size:14px;margin-right:11px}
.news-bar .stamp{margin-right:23px}
.site-header{position:absolute;top:30px;left:0;width:1073px;height:83px;background:var(--header)}
.brand{position:absolute;left:196px;top:24px;display:flex;align-items:center;gap:8px}
.brand-dot{width:32px;height:32px;border-radius:50%;background:var(--green)}
.brand-name{color:var(--white);font-size:22px;font-weight:700}
.main-nav{position:absolute;right:175px;top:34px;display:flex;font-size:14px;font-weight:300;color:var(--white)}
.main-nav span.sep{margin:0 13px}
.main-nav .active{color:var(--green)}
.backdrop{position:absolute;top:113px;left:0;width:1073px;height:1026px;
  background:linear-gradient(180deg,#9eb3c8 0%,#8c7fa3 18%,#c98fa0 34%,#f0a98a 45%,#f6c7a6 58%,#8a93a7 72%,#2d3f6e 84%,#5f7c86 93%,#3d5b66 100%)}
.slider{position:absolute;left:173px;top:145px;width:725px;height:311px;background:var(--white);border:1px solid #ccc;padding:6px}
.slide{width:100%;height:100%;background:linear-gradient(90deg,#e9edf0 0%,#d9dde0 40%,#c9b7a6 62%,#efe9e4 80%,#f2f2f2 100%);position:relative}
.slide-arrow{position:absolute;top:133px;width:28px;height:28px}
.slide-arrow.prev{left:12px}
.slide-arrow.next{right:12px}
.slide-caption{position:absolute;left:32px;bottom:22px;font-size:20px;font-weight:300;color:#333}
.content{position:absolute;left:169px;top:472px;width:735px;height:633px;background:var(--white)}
.divider{position:absolute;left:436px;top:20px;width:1px;height:483px;background:#e6e6e6}
.contact-form{position:absolute;left:69px;top:54px;width:281px}
h1,h2{font-size:19px;font-weight:500;color:var(--ink)}
.field{display:block;width:281px;border:1px solid var(--field-border);background:var(--field-bg);color:var(--muted);font-size:11.5px;font-weight:300;padding:0 14px;border-radius:2px}
.field.name{margin-top:23px;height:39px;line-height:39px}
.field.subject{margin-top:15px;height:38px;line-height:38px;position:relative}
.field.subject .handle{position:absolute;right:0;top:5px;width:31px;height:28px;border-left:1px solid #ddd}
.field.message{margin-top:15px;height:150px;padding-top:12px;line-height:1.3}
.send{position:absolute;left:164px;top:327px;width:111px;height:30px;border-radius:15px;background:linear-gradient(180deg,#7fc21c,#5b9c0a);color:var(--white);font-size:11px;font-weight:700;display:flex;align-items:center;justify-content:center;box-shadow:0 0 0 4px #f1f5ec}
.company{position:absolute;left:452px;top:54px}
.company h2{color:#555}
.company p{font-size:14px;font-weight:300;color:#333;margin-top:14px;line-height:21px}
.company p:first-of-type{margin-top:12px}
.site-footer{position:absolute;top:1139px;left:0;width:1073px;height:61px;background:var(--header);color:#ddd;text-align:center}
.footer-nav{font-size:11px;font-weight:300;margin-top:7px}
.footer-nav span.sep,.legal span.sep{margin:0 9px}
.legal{font-size:9.5px;font-weight:300;color:#aaa;margin-top:10px}
</style>
</head>
<body>
<div class="news-bar"><span class="label">Latest News :</span><span class="stamp">Last update: 23/08/2013 &nbsp;| &nbsp;16:05</span><span>Lorem Ipsum is simply dummy text of the printing and typesetting industry.</span></div>
<header class="site-header">
  <div class="brand"><span class="brand-dot"></span><span class="brand-name">Silver Harbor Trading</span></div>
  <nav class="main-nav"><span>Home</span><span class="sep">|</span><span>About us</span><span class="sep">|</span><span>Resources</span><span class="sep">|</span><span class="active">Contact us</span></nav>
</header>
<div class="backdrop" role="img" aria-label="Sunset sky over a harbor with loaded cargo container ships on the water"></div>
<section class="slider">
  <div class="slide" role="img" aria-label="Smiling support agent wearing a headset in a bright call centre">
    <svg class="slide-arrow prev" viewBox="0 0 28 28"><circle cx="14" cy="14" r="14" fill="#444" opacity=".85"/><path d="M16 8l-6 6 6 6" stroke="#fff" stroke-width="2.5" fill="none"/></svg>
    <svg class="slide-arrow next" viewBox="0 0 28 28"><circle cx="14" cy="14" r="14" fill="#444" opacity=".85"/><path d="M12 8l6 6-6 6" stroke="#fff" stroke-width="2.5" fill="none"/></svg>
    <div class="slide-caption">Contact Us</div>
  </div>
</section>
<main class="content">
  <div class="divider"></div>
  <div class="contact-form">
    <h1>Contact Us</h1>
    <div class="field name">Your Name...</div>
    <div class="field subject">Choose Subject...<span class="handle"><svg width="31" height="28" viewBox="0 0 31 28"><path d="M13 12l2.5-3 2.5 3zM13 16l2.5 3 2.5-3z" fill="#777"/></svg></span></div>
    <div class="field message">Your Message...</div>
    <div class="send">Send Message</div>
  </div>
  <div class="company">
    <h2>Silver Harbor Trading</h2>
    <p>4250 Harbor View Ave. # 118</p>
    <p>Bayside Park, CA 90999</p>
    <p>Tel.: (555) 014-2280</p>
    <p>Fax: (555) 014-2291</p>
    <p>Email us: info@maplecrest-intl.example</p>
  </div>
</main>
<footer class="site-footer">
  <div class="footer-nav"><span>Home</span><span class="sep">|</span><span>About us</span><span class="sep">|</span><span>Resources</span><span class="sep">|</span><span>Contact us</span></div>
  <div class="legal"><span>©2013 Company Name , All Rights Reserved</span><span class="sep">|</span><span>Privacy Policy</span><span class="sep">|</span><span>Terms &amp; Conditions</span></div>
</footer>
</body>
</html>
```